Tech business card design

We need an amazing business card design for our new business 'Pexla' a marketing tech startup based in Sydney, Australia. We provide an online marketplace for businesses to search and buy advertising media, connect with service providers and learn more about marketing. We wish to communicate 'cool tech', reliability and professionalism and design based around our logo.

Target Market(s)

Business Owners

Contact Information for Business Card

Name
Position
Email Address
Website
Phone Number

Font styles to use
Other font styles liked:
• Avenir & Avenir Next

Colors

Designer to choose colors to be used in the design.

```html
<!DOCTYPE html>
<html lang="en">
<head>
<meta charset="utf-8">
<title>Pexla Business Card</title>
<link rel="stylesheet" href="https://fonts.googleapis.com/css2?family=Nunito+Sans:wght@400;600;800&display=swap">
<style>
  :root {
    --navy: #13133a;
    --blue: #1a6cc2;
    --blue-soft: #2c82d6;
    --white: #ffffff;
    --paper: #e9ebee;
    --ink: #1c1c45;
    --muted: #55587a;
    --site-tint: #d9dbe8;
  }
  * { box-sizing: border-box; margin: 0; padding: 0; }
  html, body {
    width: 1200px; height: 900px; overflow: hidden;
    background: var(--paper);
    font-family: "Nunito Sans", "Avenir Next", Avenir, sans-serif;
  }
  .sheet {
    width: 1200px; height: 900px;
    display: flex; align-items: center; justify-content: center; gap: 40px;
  }
  .card {
    position: relative;
    width: 540px; height: 330px;
    overflow: hidden;
    box-shadow: 0 6px 18px rgba(20, 20, 60, 0.15);
  }
  .card-art { position: absolute; inset: 0; width: 100%; height: 100%; }
  .card--front { background: var(--navy); }
  .card--back { background: var(--white); }

  .wordmark {
    font-weight: 800;
    letter-spacing: -1px;
    line-height: 1;
    display: inline-flex; align-items: flex-start; gap: 3px;
  }
  .wordmark .tm { font-size: 9px; font-weight: 800; letter-spacing: 0; margin-top: 6px; }

  .front-brand {
    position: absolute; left: 205px; top: 118px;
    color: var(--white);
    display: flex; flex-direction: column; align-items: flex-end;
  }
  .front-brand .wordmark { font-size: 74px; }
  .front-brand .site {
    margin-top: 4px; margin-right: 14px;
    font-size: 14px; letter-spacing: 0.5px; color: var(--site-tint); font-weight: 400;
  }

  .back-brand {
    position: absolute; left: 190px; top: 190px;
    color: var(--ink);
  }
  .back-brand .wordmark { font-size: 64px; }

  .contact {
    position: absolute; left: 318px; top: 48px;
    color: var(--ink);
  }
  .contact .name { font-size: 19px; font-weight: 600; }
  .contact .role { font-size: 11px; color: var(--muted); margin-bottom: 12px; }
  .contact ul { list-style: none; }
  .contact li {
    display: flex; align-items: center; gap: 8px;
    font-size: 13px; line-height: 20px; color: var(--ink);
  }
  .contact li svg { width: 13px; height: 13px; flex: none; }
</style>
</head>
<body>
<main class="sheet">

  <section class="card card--front" aria-label="Card front">
    <svg class="card-art" viewBox="0 0 540 330" aria-hidden="true">
      <path d="M0 0 H60 Q0 170 70 330 H0 Z" fill="var(--white)"/>
      <path d="M60 0 H86 Q24 170 96 330 H70 Q0 170 60 0 Z" fill="var(--blue)"/>
      <path d="M86 0 Q40 170 96 330 H120 Q62 170 104 0 Z" fill="rgba(255,255,255,0.05)"/>
    </svg>
    <div class="front-brand">
      <div class="wordmark">pexla<span class="tm">TM</span></div>
      <div class="site">www.pexlamedia.com.au</div>
    </div>
  </section>

  <section class="card card--back" aria-label="Card back">
    <svg class="card-art" viewBox="0 0 540 330" aria-hidden="true">
      <path d="M0 0 H170 Q70 150 130 330 H0 Z" fill="var(--navy)"/>
      <path d="M170 0 H186 Q92 150 152 330 H130 Q70 150 170 0 Z" fill="var(--blue)"/>
      <path d="M186 0 H200 Q112 150 168 330 H152 Q92 150 186 0 Z" fill="var(--blue-soft)" opacity="0.35"/>
    </svg>
    <div class="contact">
      <p class="name">Marcus Reid</p>
      <p class="role">Founder | Director</p>
      <ul>
        <li>
          <svg viewBox="0 0 14 14"><rect x="3" y="0.5" width="8" height="13" rx="1.5" fill="none" stroke="var(--ink)" stroke-width="1.3"/><circle cx="7" cy="11" r="0.9" fill="var(--ink)"/></svg>
          +61 (0)412 558 203
        </li>
        <li>
          <svg viewBox="0 0 14 14"><rect x="0.5" y="2.5" width="13" height="9" fill="var(--ink)"/><path d="M0.5 2.5 L7 8 L13.5 2.5" fill="none" stroke="var(--white)" stroke-width="1.1"/></svg>
          marcus@pexlamedia.com.au
        </li>
        <li>
          <svg viewBox="0 0 14 14"><circle cx="7" cy="7" r="6.3" fill="var(--ink)"/><path d="M1 7 H13 M7 0.8 Q3.5 7 7 13.2 M7 0.8 Q10.5 7 7 13.2" fill="none" stroke="var(--white)" stroke-width="0.9"/></svg>
          www.pexlamedia.com.au
        </li>
      </ul>
    </div>
    <div class="back-brand">
      <div class="wordmark">pexla<span class="tm">TM</span></div>
    </div>
  </section>

</main>
</body>
</html>
```